WebApp for IoT (Vexa lights and Kirra/Brelline)

I am going to create my own dashbord for Quillet Pro (See other examples on https://quillet.example/) But I want it much more flexible and advanced.
One page per room (So I can have an Zanbo in each room with all functions just for that room) and include controls for light (both overall for the room and in an popupwindow all lightbulbs n the room - se more about how its done in Torvald Vexa app on https://www.torvald-vexa.example/en-us/explore-vexa/apps/bridge) aswell as set volume/track for Kirra.

I want the final solution to be "skinable" so I can choose from Blue-CSS to Green-CSS etc, but at this moment I only want ONE color!

I have added an PDF with the functions I am thinking of, but the design is for you to create!

Please have in mind it will be running on Zanbos on the wall, and in the mobile.

For the moment I only want an PSD of the "Room page", "Light popup" and "Sound Popup", but I might contract the winner to get HTML/CSS as second step.

```html
<!DOCTYPE html>
<html lang="en">
<head>
<meta charset="utf-8">
<title>Room dashboards – Kitchen &amp; Bedroom</title>
<link rel="stylesheet" href="https://fonts.googleapis.com/css2?family=Poppins:wght@400;500;600&display=swap">
<style>
  :root {
    --board: #d6d6d6;
    --overlay: rgba(40, 40, 40, 0.72);
    --white: #ffffff;
    --ink: #1c1c1c;
    --chip: rgba(160, 160, 160, 0.85);
    --chip-dim: rgba(150, 150, 150, 0.7);
    --panel: rgba(120, 120, 120, 0.35);
    --amber: #f2a20c;
    --vol-green: #22ff2a;
    --vol-yellow: #c8d200;
    --vol-orange: #ff8a00;
    --vol-red: #ff1a00;
  }
  * { box-sizing: border-box; margin: 0; padding: 0; }
  html, body { width: 808px; height: 1200px; overflow: hidden; }
  body {
    background: var(--board);
    font-family: "Poppins", sans-serif;
    color: var(--white);
    position: relative;
  }
  .room-screen {
    position: absolute;
    left: 60px;
    width: 675px;
    height: 506px;
    overflow: hidden;
    box-shadow: 0 2px 6px rgba(0,0,0,0.15);
  }
  .room-screen--kitchen { top: 64px; }
  .room-screen--bedroom { top: 622px; }

  .room-photo { position: absolute; inset: 0; }
  .room-photo--kitchen {
    background: linear-gradient(180deg, #cfcfcc 0%, #bdbab4 45%, #8a7a68 80%, #5e4a3a 100%);
  }
  .room-photo--bedroom {
    background:
      radial-gradient(circle at 80% 55%, #d9d3c8 0%, rgba(217,211,200,0) 35%),
      linear-gradient(180deg, #c9c9c6 0%, #b4b3ae 50%, #9a9892 100%);
  }
  .room-shade { position: absolute; inset: 0; background: var(--overlay); }

  .room-title {
    position: absolute; top: 24px; left: 0; right: 0;
    text-align: center; font-weight: 600; font-size: 31px; letter-spacing: 0.3px;
  }

  .round-chip {
    position: absolute; width: 46px; height: 46px; border-radius: 50%;
    display: flex; align-items: center; justify-content: center;
  }
  .round-chip--grey { background: var(--chip); }
  .round-chip--white { background: var(--white); color: var(--ink); }
  .round-chip--dim { background: var(--chip-dim); }

  .temperature { left: 34px; top: 87px; font-size: 15px; font-weight: 500; }
  .calendar-button { left: 596px; top: 87px; }

  .clock {
    position: absolute; right: 94px; top: 94px;
    text-align: right; font-size: 9.5px; font-weight: 600; line-height: 19px;
  }

  .light-button { left: 34px; top: 168px; }
  .sound-button { left: 34px; top: 231px; }

  .slider {
    position: absolute; top: 168px; width: 48px; height: 156px; border-radius: 24px;
  }
  .slider--light { left: 101px; background: linear-gradient(180deg, #ffffff 0%, #8a8a8a 45%, #000000 100%); }
  .slider-knob {
    position: absolute; left: 5px; top: 73px; width: 38px; height: 38px; border-radius: 50%;
    border: 5px solid var(--white); background: #3a3a3a;
  }
  .slider--volume { left: 170px; background: rgba(170,170,170,0.55); overflow: hidden; }
  .volume-level {
    position: absolute; left: 0; right: 0; bottom: 0; height: 108px;
    background: linear-gradient(180deg, var(--vol-green) 0%, var(--vol-yellow) 35%, var(--vol-orange) 65%, var(--vol-red) 100%);
    border-radius: 24px 24px 24px 24px / 6px 6px 24px 24px;
  }

  .slider-caption {
    position: absolute; top: 332px; width: 70px; text-align: center;
    font-size: 12.5px; font-weight: 500;
  }
  .slider-caption--light { left: 90px; }
  .slider-caption--volume { left: 159px; }
  .slider-caption svg { display: block; margin: 6px auto 0; }

  .lights-panel {
    position: absolute; left: 474px; top: 151px; width: 168px;
    border: 2.5px solid var(--white); border-radius: 13px; background: var(--panel);
  }
  .lights-panel--kitchen { height: 226px; }
  .lights-panel--bedroom { height: 288px; }
  .light-row {
    position: absolute; left: 0; right: 0; height: 46px;
    display: flex; align-items: center; justify-content: flex-end; padding-right: 20px; gap: 14px;
  }
  .light-row .light-name { font-size: 15px; font-weight: 600; letter-spacing: -0.3px; }
  .light-row .round-chip { position: static; }
</style>
</head>
<body>

<svg width="0" height="0" style="position:absolute">
  <defs>
    <symbol id="icon-bulb" viewBox="0 0 24 24">
      <path d="M12 2.5a6.5 6.5 0 0 0-3.8 11.8c.6.5.9 1.1.9 1.8V17h5.8v-.9c0-.7.3-1.3.9-1.8A6.5 6.5 0 0 0 12 2.5z" fill="none" stroke="currentColor" stroke-width="1.8"/>
      <rect x="9.1" y="18.2" width="5.8" height="1.8" rx="0.6" fill="currentColor"/>
      <rect x="10" y="21" width="4" height="1.6" rx="0.6" fill="currentColor"/>
      <path d="M12 6.5a3 3 0 0 1 3 3" fill="none" stroke="currentColor" stroke-width="1.4" stroke-linecap="round"/>
    </symbol>
    <symbol id="icon-speaker" viewBox="0 0 24 24">
      <path d="M3 9h4l5-4v14l-5-4H3z" fill="currentColor"/>
      <path d="M15 9a4 4 0 0 1 0 6M17.5 6.5a7.5 7.5 0 0 1 0 11" fill="none" stroke="currentColor" stroke-width="1.8" stroke-linecap="round"/>
    </symbol>
    <symbol id="icon-calendar" viewBox="0 0 24 24">
      <rect x="3.5" y="5" width="17" height="15.5" rx="1.5" fill="none" stroke="currentColor" stroke-width="1.6"/>
      <path d="M3.5 9.5h17M8 3v4M16 3v4M7 12.5h10M7 15.5h10M10 10v9.5M14 10v9.5" stroke="currentColor" stroke-width="1.2"/>
    </symbol>
  </defs>
</svg>

<section class="room-screen room-screen--kitchen">
  <div class="room-photo room-photo--kitchen" role="img" aria-label="Photo of a white kitchen with wooden floor"></div>
  <div class="room-shade"></div>
  <h1 class="room-title">KITCHEN</h1>
  <div class="round-chip round-chip--grey temperature">23°</div>
  <div class="clock">2022-07-14<br>15:23</div>
  <div class="round-chip round-chip--grey calendar-button"><svg width="16" height="16"><use href="#icon-calendar"/></svg></div>
  <div class="round-chip round-chip--white light-button"><svg width="22" height="22"><use href="#icon-bulb"/></svg></div>
  <div class="slider slider--light"><div class="slider-knob"></div></div>
  <div class="slider-caption slider-caption--light">Light<svg width="11" height="11"><use href="#icon-bulb"/></svg></div>
  <div class="lights-panel lights-panel--kitchen">
    <div class="light-row" style="top:17px"><span class="light-name">LIGHT 1</span><span class="round-chip round-chip--white" style="color:var(--amber)"><svg width="16" height="16"><use href="#icon-bulb"/></svg></span></div>
    <div class="light-row" style="top:86px"><span class="light-name">LIGHT 2</span><span class="round-chip round-chip--dim" style="color:var(--amber)"><svg width="16" height="16"><use href="#icon-bulb"/></svg></span></div>
    <div class="light-row" style="top:155px"><span class="light-name">LIGHT 3</span><span class="round-chip round-chip--dim" style="color:var(--amber)"><svg width="16" height="16"><use href="#icon-bulb"/></svg></span></div>
  </div>
</section>

<section class="room-screen room-screen--bedroom">
  <div class="room-photo room-photo--bedroom" role="img" aria-label="Photo of a bedroom with bed, bedside lamps and lounge chair"></div>
  <div class="room-shade"></div>
  <h1 class="room-title">BEDROOM</h1>
  <div class="round-chip round-chip--grey temperature">23°</div>
  <div class="clock">2022-07-14<br>15:23</div>
  <div class="round-chip round-chip--grey calendar-button"><svg width="16" height="16"><use href="#icon-calendar"/></svg></div>
  <div class="round-chip round-chip--white light-button"><svg width="22" height="22"><use href="#icon-bulb"/></svg></div>
  <div class="round-chip round-chip--white sound-button"><svg width="22" height="22"><use href="#icon-speaker"/></svg></div>
  <div class="slider slider--light"><div class="slider-knob"></div></div>
  <div class="slider slider--volume"><div class="volume-level"></div></div>
  <div class="slider-caption slider-caption--light">Light<svg width="11" height="11"><use href="#icon-bulb"/></svg></div>
  <div class="slider-caption slider-caption--volume">Volume<svg width="12" height="12"><use href="#icon-speaker"/></svg></div>
  <div class="lights-panel lights-panel--bedroom">
    <div class="light-row" style="top:17px"><span class="light-name">LIGHT 1</span><span class="round-chip round-chip--white" style="color:var(--amber)"><svg width="16" height="16"><use href="#icon-bulb"/></svg></span></div>
    <div class="light-row" style="top:86px"><span class="light-name">LIGHT 2</span><span class="round-chip round-chip--dim" style="color:var(--amber)"><svg width="16" height="16"><use href="#icon-bulb"/></svg></span></div>
    <div class="light-row" style="top:155px"><span class="light-name">LIGHT 3</span><span class="round-chip round-chip--dim" style="color:var(--amber)"><svg width="16" height="16"><use href="#icon-bulb"/></svg></span></div>
    <div class="light-row" style="top:224px"><span class="light-name">LIGHT 4</span><span class="round-chip round-chip--dim" style="color:var(--amber)"><svg width="16" height="16"><use href="#icon-bulb"/></svg></span></div>
  </div>
</section>

</body>
</html>
```